Legal firm website redesign

Existing site for Sydney CBD lawyer needs clean and professional redesign - http://brintonlaw.com.au

The site will be viewed by a wide range of users: businesses, individuals, referral partners and other lawyers.

Please see the list of must haves for further details

Target Market(s)

Businesses, individuals, referral partners and other lawyers

Industry/Entity Type

Lawyer

Requirements
Must have
• Prominent display of phone number.
List of services down the left hand side of the site (5x services or so).
Search box in header.
Please use the greys and blues from the existing header.
New header must include the wording "Efficiency - Fulfillment - Integrity - Teamwork"

```html
<!DOCTYPE html>
<html lang="en">
<head>
<meta charset="utf-8">
<title>Brinton Law</title>
<link rel="stylesheet" href="https://fonts.googleapis.com/css2?family=Open+Sans:wght@400;600;700&display=swap">
<style>
:root{
  --blue:#0a74c4;
  --blue-dark:#0560a8;
  --grey-band:#5e5e5e;
  --text:#333;
  --muted:#555;
  --line:#d9d9d9;
  --white:#fff;
}
*{margin:0;padding:0;box-sizing:border-box}
html,body{width:1200px;height:988px;overflow:hidden;background:var(--white);font-family:"Open Sans",sans-serif;color:var(--text)}
.canvas{position:relative;width:1200px;height:988px}
.header-band{position:absolute;left:0;top:0;width:1200px;height:620px;background:var(--grey-band)}
.topbar{position:absolute;left:25px;top:0;width:1152px;height:40px;background:var(--white);border-top:7px solid var(--blue);font-size:13px;color:#666;text-align:right;padding:9px 14px 0 0}
.brand{position:absolute;left:42px;top:62px;font-size:52px;font-weight:700;color:var(--white);letter-spacing:-1px}
.phone{position:absolute;right:33px;top:76px;font-size:31px;font-weight:600;color:var(--white)}
.panel{position:absolute;left:25px;top:145px;width:1152px;height:749px;background:var(--white);box-shadow:0 2px 3px rgba(0,0,0,.15)}
.nav{position:absolute;left:38px;top:158px;width:1126px;height:35px;background:linear-gradient(#fdfdfd,#e9e9e9);border:1px solid #e0e0e0}
.nav a{position:absolute;top:0;height:33px;line-height:33px;font-size:15.5px;color:var(--blue);text-decoration:none;transform:translateX(-50%)}
.nav a.active{left:0;transform:none;width:118px;text-align:center;background:linear-gradient(#2b92e0,var(--blue-dark));color:var(--white)}
.search{position:absolute;left:801px;top:4px;display:flex}
.search input{width:232px;height:24px;border:1px solid #ccc;background:var(--white)}
.search button{width:76px;height:24px;border:0;margin-left:2px;background:linear-gradient(#2b92e0,var(--blue-dark));color:var(--white);font:600 14px "Open Sans",sans-serif}
.section-title{position:absolute;font-size:22px;font-weight:400;color:var(--blue)}
.recent{position:absolute;left:55px;top:237px;width:340px;list-style:none;font-size:14.6px;line-height:21px}
.recent li{margin-bottom:2.4px}
.hero{position:absolute;left:408px;top:201px;width:756px;height:406px;background:radial-gradient(ellipse at 35% 60%,#d0621a,#8a2a08 55%,#3a1004)}
.hero-words{position:absolute;left:452px;top:238px;font-size:32px;line-height:41px;color:var(--white)}
.hero-words span::before{content:"";display:inline-block;width:10px;height:10px;border-radius:50%;background:var(--white);margin:0 6px 7px 0}
.hero-words span+span{margin-left:10px}
.about{position:absolute;left:43px;top:682px;width:600px;font-size:15.2px;line-height:21px}
.about p{margin-bottom:8px}
.book{position:absolute;left:1040px;top:700px;width:104px;height:146px;background:linear-gradient(160deg,#4a4a4a,#111);border-radius:4px;z-index:1}
.services{position:absolute;left:696px;top:672px;list-style:none;font-size:14.6px;line-height:23.5px;z-index:2}
.services li::before{content:"";display:inline-block;width:8px;height:8px;border-radius:50%;background:#555;margin:0 8px 2px 0}
.more{position:absolute;top:863px;font-size:12.5px;color:var(--blue);text-decoration:none}
.footer-links{position:absolute;left:45px;top:929px;font-size:12.4px;color:var(--muted)}
.footer-links a{color:var(--muted);text-decoration:none}
.legal{position:absolute;right:39px;top:929px;font-size:12.4px;color:var(--muted)}
.bottom-bar{position:absolute;left:25px;top:979px;width:1152px;height:9px;background:var(--blue)}
</style>
</head>
<body>
<div class="canvas">
  <div class="header-band"></div>
  <div class="topbar">Facsimile : (02) 9000 4822 | Email :&nbsp; info@brintonlaw.com.au</div>
  <div class="brand">brinton law</div>
  <div class="phone">Telephone (02) 9000 4821</div>

  <div class="panel"></div>
  <nav class="nav">
    <a class="active" href="#">Home</a>
    <a href="#" style="left:188px">About Us</a>
    <a href="#" style="left:340px">Areas of Law</a>
    <a href="#" style="left:503px">Publications</a>
    <a href="#" style="left:649px">Contact</a>
    <form class="search"><input type="text" aria-label="Search"><button type="button">Search</button></form>
  </nav>

  <h2 class="section-title" style="left:39px;top:202px">Recent Additions</h2>
  <ul class="recent">
    <li>Commencement of the Succession<br>Act 2006 25.03.08</li>
    <li>Is that will valid? 15.01.08</li>
    <li>Labor's proposed changes to IR laws 14.12.07</li>
    <li>Should you make your own will? 14.11.07</li>
    <li>Illegal workers 14.08.07</li>
    <li>Employees' liability for misleading or deceptive<br>conduct 14.08.07</li>
    <li>Correct use of ACNs and ABNs 14.08.07</li>
    <li>Power of Attorney Infosheet 10.08.07</li>
    <li>Intestate Estates Infosheet 08.08.07</li>
    <li>Estate Planning Infosheet 07.06.07</li>
    <li>Special Disability Trusts Infosheet 18.05.07</li>
    <li>Testamentary Trusts Infosheet 17.05.07</li>
    <li>Appointment of an Enduring Guardian<br>Infosheet 15.05.07</li>
  </ul>

  <div class="hero" role="img" aria-label="Photo of a judge's gavel and brass scales of justice in warm light"></div>
  <div class="hero-words"><span>Efficiency</span><span>Fulfillment</span><br><span>Integrity</span><span>Teamwork</span></div>

  <h2 class="section-title" style="left:43px;top:634px">About Brinton Law</h2>
  <div class="about">
    <p>Brinton Law is a dynamic commercial law firm in the CBD of Sydney providing services to corporate, small business and private clients.</p>
    <p>Brinton Law brings together over 30 years of experience in legal practice.</p>
    <p>The strong focus of the firm is on commercial law and estate planning.</p>
    <p>Brinton Law is committed to providing quality legal services in helping its clients achieve their objectives by providing a proactive understanding of its clients' businesses and creative legal solutions.</p>
  </div>
  <a class="more" href="#" style="left:574px">view more</a>

  <h2 class="section-title" style="left:694px;top:636px">Commercial/Business Transactions</h2>
  <div class="book" role="img" aria-label="Illustration of a law book with a gavel"></div>
  <ul class="services">
    <li>Buying and selling businesses and companies</li>
    <li>Financing</li>
    <li>Leasing</li>
    <li>Property transactions</li>
    <li>Joint ventures</li>
    <li>Business restructuring</li>
    <li>Contract review and advice</li>
    <li>Employment Law Documentation, e.g. AWAs</li>
  </ul>
  <a class="more" href="#" style="left:1100px">view more</a>

  <div class="footer-links"><a href="#">Home</a> &nbsp;|&nbsp; <a href="#">About Us</a> &nbsp;|&nbsp; <a href="#">Areas of Law</a> &nbsp;|&nbsp; <a href="#">Publications</a> &nbsp;|&nbsp; <a href="#">Contact</a></div>
  <div class="legal">© 2012 Brinton Law - Terms of Service - Privacy Policy - Program Policies</div>
  <div class="bottom-bar"></div>
</div>
</body>
</html>
```